Enterprise image desing

The designs are for a fashion store for young men and women.
Updates

Los diseƱos parecen similares

Target Market(s)

Young

Font styles to use
Sans Serif

Colors
ec1f27
ffffff
1b1b1b

Requirements
Must have
• Use clean and modern sources
Nice to have
• n / a
Should not have
• n / a

```html
<!DOCTYPE html>
<html lang="en">
<head>
<meta charset="utf-8">
<title>Veltora Stationery</title>
<link rel="stylesheet" href="https://fonts.googleapis.com/css2?family=Work+Sans:wght@400;500;700&display=swap">
<style>
  :root {
    --navy: #07284a;
    --navy-deep: #06243f;
    --red: #ec1f27;
    --white: #ffffff;
    --paper: #f4f4f5;
    --ink: #1b1b1b;
    --muted: #9a9a9a;
    --stage: #adadad;
  }
  * { margin: 0; padding: 0; box-sizing: border-box; }
  html, body { width: 1037px; height: 1200px; overflow: hidden; }
  body {
    background: var(--stage);
    font-family: "Work Sans", sans-serif;
    color: var(--ink);
    position: relative;
  }
  .piece { position: absolute; overflow: hidden; }
  .brand {
    display: flex; align-items: center; gap: 0.3em;
    font-family: "Work Sans", sans-serif; font-weight: 700;
    color: var(--navy); letter-spacing: 0.02em; position: absolute; line-height: 1;
  }
  .brand-square { width: 0.9em; height: 0.9em; background: var(--red); flex: none; }
  .brand--light { color: var(--white); }
  .band { position: absolute; left: 0; bottom: 0; width: 100%; }
  .rule { position: absolute; height: 1px; background: var(--red); }
  .contact { position: absolute; font-size: 5.6px; line-height: 1.35; color: #3a3a3a; }
  .contact li { list-style: none; display: flex; align-items: center; gap: 3px; }
  .contact li::before { content: ""; width: 3px; height: 3px; border-radius: 50%; background: var(--red); }
  .contact .web { color: var(--red); }
  .address { position: absolute; font-size: 5.6px; line-height: 1.35; text-align: right; color: #3a3a3a; }

  /* Letterhead */
  .letter-back { left: 141px; top: 104px; width: 357px; height: 486px; background: var(--navy); }
  .letterhead { left: 86px; top: 59px; width: 358px; height: 487px; background: var(--white); box-shadow: 0 2px 6px rgba(0,0,0,.25); }
  .letterhead .brand { left: 27px; top: 30px; font-size: 21px; }
  .salutation { position: absolute; left: 27px; top: 136px; font-size: 9.5px; color: var(--muted); }
  .letter-body { position: absolute; left: 27px; top: 168px; width: 306px; font-size: 6.4px; line-height: 9.2px; color: #a5a5a5; }
  .letter-body p { margin-bottom: 7px; }
  .signature { position: absolute; left: 27px; top: 380px; width: 105px; height: 14px; background: #ececec; }
  .letterhead .rule { left: 27px; width: 301px; top: 435px; }
  .letterhead .contact { left: 27px; top: 442px; }
  .letterhead .address { right: 30px; top: 442px; }

  /* Business cards */
  .card-front { left: 569px; top: 81px; width: 198px; height: 113px; background: var(--white); box-shadow: 0 2px 5px rgba(0,0,0,.25); }
  .card-front .brand { right: 13px; top: 12px; font-size: 11px; }
  .card-name { position: absolute; left: 12px; top: 48px; font-size: 6px; font-weight: 700; color: var(--red); }
  .card-role { position: absolute; left: 12px; top: 56px; font-size: 4.6px; color: #555; }
  .card-front .divider { position: absolute; left: 12px; width: 174px; top: 67px; height: 1px; background: var(--navy); }
  .card-front .contact { left: 12px; top: 73px; font-size: 4.6px; }
  .card-front .address { right: 13px; top: 73px; font-size: 4.6px; }
  .card-back { left: 780px; top: 81px; width: 197px; height: 113px; background: var(--navy); box-shadow: 0 2px 5px rgba(0,0,0,.3); }
  .card-back .brand { left: 50%; top: 48px; transform: translateX(-50%); font-size: 15px; }
  .card-back .site { position: absolute; width: 100%; top: 98px; text-align: center; font-size: 4.6px; color: var(--white); }
  .card-back .site span { color: var(--red); }

  /* Envelope */
  .envelope-back { left: 626px; top: 346px; width: 351px; height: 247px; background: var(--navy); }
  .envelope-front { left: 529px; top: 226px; width: 353px; height: 166px; background: var(--white); box-shadow: 0 2px 6px rgba(0,0,0,.25); }
  .envelope-mark { position: absolute; left: 23px; top: 18px; width: 58px; height: 58px; background: var(--red); }
  .envelope-front .rule { left: 23px; width: 307px; top: 122px; }
  .envelope-front .contact { left: 23px; top: 127px; }
  .envelope-front .address { right: 22px; top: 127px; }

  /* Folder */
  .folder-left { left: 213px; top: 686px; width: 310px; height: 450px; background: var(--navy); }
  .folder-left .ghost { position: absolute; left: 45px; top: 116px; width: 219px; height: 226px; background: var(--navy-deep); }
  .folder-left .brand { left: 43px; top: 384px; font-size: 27px; }
  .folder-right { left: 523px; top: 686px; width: 310px; height: 450px; background: var(--paper); }
  .folder-right .brand { left: 69px; top: 38px; font-size: 24px; }
  .folder-right .ghost { position: absolute; left: 47px; top: 118px; width: 220px; height: 224px; background: #f1e3e6; }
  .folder-strip { position: absolute; left: 0; top: 380px; width: 100%; height: 44px; background: var(--navy); }
  .folder-strip .contact { left: 24px; top: 12px; color: var(--white); }
  .folder-strip .address { right: 16px; top: 8px; color: var(--white); }
</style>
</head>
<body>

<!-- Letterhead -->
<div class="piece letter-back"></div>
<section class="piece letterhead">
  <div class="brand"><span class="brand-square"></span>VELTORA</div>
  <p class="salutation">Dear sir,</p>
  <div class="letter-body">
    <p>Lorem ipsum dolor sit amet, an vel recteque dissentiet, detracto albucius platonem ex vel, eros repudiandae cu. Atqui aliquando nec an, unum graece adolescens vel ad. Id odio scae has, ludico euismod atomorum ius ea, cum ea honestatis quaerendum theophrastus. Mea honestatis quaerendum theophrastus. Mea</p>
    <p>Lorem ipsum dolor sit amet, an vel recteque dissentiet, detracto albucius platonem ex vel, eros repudiandae cu. Atqui aliquando nec an, unum graece adolescens vel ad. Id odio scae has, ludico euismod atomorum ius ea, cum ea honestatis quaerendum theophrastus. Mea doming repudiandae ex, cu cum civibus assentior posidonium. Quo etiam pertinax ex, te eros repudiandae cu. Atqui aliquando nec an, unum graece adolescens vel ad. Id odio scae honestatis quaerendum theophrastus. Mea</p>
    <p>Lorem ipsum dolor sit amet, an vel recteque dissentiet, detracto albucius platonem ex vel, eros repudiandae cu. Atqui aliquando nec an, unum graece adolescens vel ad. Id odio scae has, ludico euismod atomorum ius ea, cum ea honestatis quaerendum theophrastus. Mea honestatis quaerendum theophrastus. Mea</p>
    <p>eros repudiandae cu. Atqui aliquando nec an, unum graece adolescens vel ad. Id odio scae honestatis quaerendum theophrastus. Mea posidonium. Quo etiam pertinax ex, te etiam pertinax ex, te</p>
  </div>
  <div class="signature" role="img" aria-label="Handwritten signature"></div>
  <div class="rule"></div>
  <ul class="contact">
    <li>(555) 4 210-7788</li>
    <li>hello@veltora.com</li>
    <li class="web">www.veltora.com</li>
  </ul>
  <p class="address">Calle Olmos y Avenida Sur<br>Puerto Alto - Region 4402</p>
  <svg class="band" width="358" height="14" viewBox="0 0 358 14" aria-hidden="true">
    <path d="M0 3 H230 Q238 3 244 6 L0 6 Z" fill="var(--red)"/>
    <path d="M0 9 H236 Q246 9 252 4 Q258 0 268 0 H358 V14 H0 Z" fill="var(--navy)"/>
  </svg>
</section>

<!-- Business card front -->
<section class="piece card-front">
  <div class="brand"><span class="brand-square"></span>VELTORA</div>
  <p class="card-name">MARCO IBARRA SOLIS</p>
  <p class="card-role">Director General</p>
  <div class="divider"></div>
  <ul class="contact">
    <li>(555) 4 210-7788</li>
    <li>(555) 91 306-2284</li>
    <li>mibarra@veltora.com</li>
    <li>www.veltora.com</li>
  </ul>
  <p class="address">Calle Olmos y<br>Avenida Sur, Puerto Alto<br>Region 4402</p>
  <svg class="band" width="198" height="7" viewBox="0 0 198 7" aria-hidden="true">
    <path d="M0 1 H120 Q125 1 128 2.5 L0 2.5 Z" fill="var(--red)"/>
    <path d="M0 4.5 H124 Q129 4.5 132 2 Q135 0 140 0 H198 V7 H0 Z" fill="var(--navy)"/>
  </svg>
</section>

<!-- Business card back -->
<section class="piece card-back">
  <div class="brand brand--light"><span class="brand-square"></span>VELTORA</div>
  <p class="site">www.<span>veltora</span>.com</p>
</section>

<!-- Envelope -->
<div class="piece envelope-back">
  <svg width="351" height="247" viewBox="0 0 351 247" aria-hidden="true">
    <path d="M0 0 H351 L330 115 Q328 120 320 120 H30 Q22 120 20 115 Z" fill="#e6e6e8"/>
    <path d="M20 115 Q22 120 30 120 H320 Q328 120 330 115 L351 160 V247 H0 V160 Z" fill="var(--navy)"/>
  </svg>
</div>
<section class="piece envelope-front">
  <div class="envelope-mark"></div>
  <div class="rule"></div>
  <ul class="contact">
    <li>(555) 4 210-7788</li>
    <li>hello@veltora.com</li>
    <li class="web">www.veltora.com</li>
  </ul>
  <p class="address">Calle Olmos y Avenida Sur<br>Puerto Alto - Region 4402</p>
  <svg class="band" width="353" height="14" viewBox="0 0 353 14" aria-hidden="true">
    <path d="M0 2 H185 Q192 2 197 5 L0 5 Z" fill="var(--red)"/>
    <path d="M0 8 H190 Q199 8 205 4 Q211 0 220 0 H353 V14 H0 Z" fill="var(--navy)"/>
  </svg>
</section>

<!-- Presentation folder -->
<section class="piece folder-left">
  <div class="ghost"></div>
  <div class="brand brand--light"><span class="brand-square"></span>VELTORA</div>
</section>
<section class="piece folder-right">
  <div class="brand"><span class="brand-square"></span>VELTORA</div>
  <div class="ghost"></div>
  <div class="folder-strip">
    <ul class="contact">
      <li>(555) 4 210-7788</li>
      <li>hello@veltora.com</li>
      <li class="web">www.veltora.com</li>
    </ul>
    <p class="address">Calle Olmos y Avenida Sur<br>Puerto Alto - Region 4402</p>
  </div>
</section>

</body>
</html>
```